Theme and starter template for small business powerpoint deck

We are starting a technology consulting company and would like to have a powerpoint/google slide theme and initial template. We are more concerned with the theme/colors at this point. Initial template can be pretty simple. We would want a cover slide, agenda slide, some content slides including text content, image content, a combination of both, etc. A closing slide. we have included jpg files of our logo, let us know if you would prefer eps/vector. I assume you may want exact color data as well?

Target Market(s)

Technology and Customer Experience Leadership at companies with 25 or more employees

Industry/Entity Type

Technology Consulting

Font styles to use
Sans Serif

Colors
0054AA
0677BA
7BADD7
CADEEF
E8F1F8

Requirements
Must have
• I have attached JPG and EPS and vector files to project. I would like to stay with those colors but open to slight variation if recommended.

```html
<!DOCTYPE html>
<html lang="en">
<head>
<meta charset="utf-8">
<title>Vantrix – Presentation Theme</title>
<link rel="stylesheet" href="https://fonts.googleapis.com/css2?family=Open+Sans:wght@700;800&family=Poppins:wght@400;500;600;700&display=swap">
<style>
  :root{
    --navy:#0054AA;
    --ocean:#0677BA;
    --sky:#7BADD7;
    --mist:#CADEEF;
    --ice:#E8F1F8;
    --accent:#C8323B;
    --ink:#1d1d1f;
    --body:#3a3a3a;
    --page:#F5F5F5;
  }
  html,body{margin:0;padding:0;overflow:hidden;}
  body{width:1105px;height:1200px;background:var(--page);position:relative;font-family:'Poppins',sans-serif;}
  .slide{position:absolute;width:481px;height:270px;display:block;background:#fff;}
  .col-left{left:48px;} .col-right{left:577px;}
  .row-1{top:28px;} .row-2{top:313px;} .row-3{top:597px;} .row-4{top:882px;}
  .heading{font-family:'Open Sans',sans-serif;font-weight:800;fill:var(--navy);}
  .heading.light{fill:#fff;}
  .subtitle{font-family:'Poppins',sans-serif;font-weight:400;fill:var(--navy);}
  .body{font-family:'Poppins',sans-serif;font-weight:400;fill:var(--body);}
  .body.light{fill:#fff;}
  .label{font-family:'Poppins',sans-serif;font-weight:600;}
  .brand{font-family:'Poppins',sans-serif;font-weight:700;fill:var(--ink);}
  .footer-band{fill:var(--mist);}
  .page-dot{fill:var(--navy);}
  .page-num{font-family:'Poppins',sans-serif;font-weight:600;font-size:11px;fill:#fff;}
  .icon{fill:none;stroke:#fff;stroke-width:2;stroke-linecap:round;stroke-linejoin:round;}
  .icon.dark{stroke:var(--ink);stroke-width:1.6;}
</style>
</head>
<body>

<!-- Cover -->
<svg class="slide col-left row-1" viewBox="0 0 804 452" aria-label="Cover slide">
  <defs>
    <linearGradient id="cover-photo-a" x1="0" y1="0" x2="1" y2="1"><stop offset="0" stop-color="#dfe5ec"/><stop offset="1" stop-color="#6f86a3"/></linearGradient>
    <linearGradient id="cover-photo-b" x1="0" y1="0" x2="1" y2="1"><stop offset="0" stop-color="#5d86b5"/><stop offset="1" stop-color="#0f2c57"/></linearGradient>
    <linearGradient id="cover-photo-c" x1="0" y1="0" x2="1" y2="1"><stop offset="0" stop-color="#2f86c9"/><stop offset="1" stop-color="#071d3f"/></linearGradient>
  </defs>
  <rect width="804" height="452" fill="#fff"/>
  <text class="brand" x="23" y="58" font-size="44" letter-spacing="1">VANTRIX</text>
  <rect x="226" y="30" width="22" height="22" fill="var(--accent)"/>
  <rect x="23" y="64" width="306" height="4" rx="2" fill="#9a9a9a"/>
  <text class="heading" x="23" y="206" font-size="44">Presentation</text>
  <text class="subtitle" x="23" y="243" font-size="30">Title Goes Here</text>
  <text class="body" font-size="16"><tspan x="22" y="275">Excepteur sint occaecat cupidatat</tspan><tspan x="22" y="300">non proident, sunt in culpa qui officia</tspan><tspan x="22" y="325">deserunt mollit ani</tspan></text>
  <polygon points="540,0 408,226 670,226" fill="url(#cover-photo-a)" role="img" aria-label="Photo of colleagues working together at a computer"/>
  <polygon points="408,226 276,452 540,452" fill="url(#cover-photo-b)" role="img" aria-label="Photo of a team reviewing a tablet in a server room"/>
  <polygon points="670,226 540,452 804,452" fill="url(#cover-photo-c)" role="img" aria-label="Photo of hands holding a glowing digital globe"/>
</svg>

<!-- Three content -->
<svg class="slide col-right row-1" viewBox="0 0 804 452" aria-label="Three content slide">
  <defs>
    <linearGradient id="three-photo" x1="0" y1="0" x2="1" y2="1"><stop offset="0" stop-color="#4f86c2"/><stop offset="1" stop-color="#1e4f8c"/></linearGradient>
  </defs>
  <rect width="804" height="452" fill="#fff"/>
  <rect width="804" height="206" fill="url(#three-photo)" role="img" aria-label="Photo of hands working on a laptop with digital overlay"/>
  <text class="heading light" x="402" y="74" font-size="34" text-anchor="middle">Three Content Slide Goes Here</text>
  <rect x="377" y="96" width="50" height="5" fill="#fff"/>
  <polygon points="188,127 28,397 348,397" fill="var(--ocean)"/>
  <polygon points="243,126 562,126 402,397" fill="var(--ocean)"/>
  <polygon points="618,127 458,397 778,397" fill="var(--ocean)"/>
  <g class="icon"><circle cx="188" cy="228" r="14"/><circle cx="188" cy="224" r="4"/><path d="M180 236 q8 -8 16 0"/></g>
  <g class="icon"><circle cx="402" cy="282" r="12"/><path d="M402 270 v-6 M402 294 v6 M390 282 h-6 M414 282 h6"/><circle cx="402" cy="282" r="4"/></g>
  <g class="icon"><circle cx="618" cy="232" r="13"/><circle cx="618" cy="232" r="5"/><path d="M603 232 v6 M633 232 v6"/></g>
  <g fill="#fff">
    <text class="label" x="188" y="288" font-size="15" text-anchor="middle">Nemo enim</text>
    <text class="body light" font-size="11" text-anchor="middle"><tspan x="188" y="309">Excepteur sint occaecat cupida</tspan><tspan x="188" y="327">tnon proident, sunt in culpa qui</tspan><tspan x="188" y="346">officinim ipsam voluptatem quia</tspan><tspan x="188" y="364">voluptas sit aspernatur aut odit aut</tspan><tspan x="188" y="382">quia consequun.</tspan></text>
    <text class="label" x="402" y="154" font-size="15" text-anchor="middle">Nemo enim</text>
    <text class="body light" font-size="11" text-anchor="middle"><tspan x="402" y="174">Excepteur sint occaecat cupida</tspan><tspan x="402" y="192">tnon proident, sunt in culpa qui</tspan><tspan x="402" y="211">officinim ipsam voluptatem quia</tspan><tspan x="402" y="229">voluptas sit aspernatur aut odit</tspan><tspan x="402" y="248">quia consequun.</tspan></text>
    <text class="label" x="618" y="288" font-size="15" text-anchor="middle">Nemo enim</text>
    <text class="body light" font-size="11" text-anchor="middle"><tspan x="618" y="309">Excepteur sint occaecat cupida</tspan><tspan x="618" y="327">tnon proident, sunt in culpa qui</tspan><tspan x="618" y="346">officinim ipsam voluptatem quia</tspan><tspan x="618" y="364">voluptas sit aspernatur aut odit aut</tspan><tspan x="618" y="382">quia consequun.</tspan></text>
  </g>
  <rect class="footer-band" y="415" width="804" height="37"/>
  <text class="brand" x="19" y="439" font-size="15">VANTRIX</text>
  <rect x="88" y="429" width="8" height="8" fill="var(--accent)"/>
  <circle class="page-dot" cx="782" cy="433" r="10"/><text class="page-num" x="782" y="437" text-anchor="middle">5</text>
</svg>

<!-- Agenda -->
<svg class="slide col-left row-2" viewBox="0 0 804 452" aria-label="Agenda slide">
  <defs>
    <linearGradient id="agenda-photo" x1="0" y1="0" x2="1" y2="1"><stop offset="0" stop-color="#1f5aa3"/><stop offset="1" stop-color="#0a1f45"/></linearGradient>
  </defs>
  <rect width="804" height="452" fill="#fff"/>
  <polygon points="206,30 10,361 402,361" fill="url(#agenda-photo)" role="img" aria-label="Photo of a team working together in a data center"/>
  <text class="heading light" font-size="36" text-anchor="middle"><tspan x="206" y="227">Agenda</tspan><tspan x="211" y="266">Slide</tspan></text>
  <rect x="181" y="289" width="50" height="5" fill="#fff"/>
  <g class="agenda-list">
    <g transform="translate(468,50)"><polygon points="0,-11 12,9 -12,9" fill="var(--accent)"/><text class="page-num" y="6" text-anchor="middle" font-size="10">1</text><text class="body" x="29" y="5" font-size="14.5" fill="var(--ink)">Sed ut perspiciatis unde omnis</text></g>
    <g transform="translate(468,95)"><polygon points="0,-11 12,9 -12,9" fill="var(--accent)"/><text class="page-num" y="6" text-anchor="middle" font-size="10">2</text><text class="body" x="29" y="5" font-size="14.5">Iste natus error sit voluptatem accusant</text></g>
    <g transform="translate(468,140)"><polygon points="0,-11 12,9 -12,9" fill="var(--accent)"/><text class="page-num" y="6" text-anchor="middle" font-size="10">3</text><text class="body" x="29" y="5" font-size="14.5">Totam rem aperiam sint occaecat</text></g>
    <g transform="translate(468,184)"><polygon points="0,-11 12,9 -12,9" fill="var(--accent)"/><text class="page-num" y="6" text-anchor="middle" font-size="10">4</text><text class="body" x="29" y="5" font-size="14.5">Cupidatat non proident</text></g>
    <g transform="translate(468,229)"><polygon points="0,-11 12,9 -12,9" fill="var(--accent)"/><text class="page-num" y="6" text-anchor="middle" font-size="10">5</text><text class="body" x="29" y="5" font-size="14.5">Sunt in culpa qui officia deserunt mollit</text></g>
    <g transform="translate(468,274)"><polygon points="0,-11 12,9 -12,9" fill="var(--accent)"/><text class="page-num" y="6" text-anchor="middle" font-size="10">6</text><text class="body" x="29" y="5" font-size="14.5">Totam rem aperiam sint occaecat</text></g>
    <g transform="translate(468,319)"><polygon points="0,-11 12,9 -12,9" fill="var(--accent)"/><text class="page-num" y="6" text-anchor="middle" font-size="10">7</text><text class="body" x="29" y="5" font-size="14.5">Cupidatat non proident</text></g>
    <g transform="translate(468,364)"><polygon points="0,-11 12,9 -12,9" fill="var(--accent)"/><text class="page-num" y="6" text-anchor="middle" font-size="10">8</text><text class="body" x="29" y="5" font-size="14.5">Sunt in culpa qui officia deserunt</text></g>
  </g>
  <rect class="footer-band" y="415" width="804" height="37"/>
  <text class="brand" x="10" y="439" font-size="15">VANTRIX</text>
  <rect x="79" y="429" width="8" height="8" fill="var(--accent)"/>
  <circle class="page-dot" cx="781" cy="434" r="10"/><text class="page-num" x="781" y="438" text-anchor="middle">2</text>
</svg>

<!-- Timeline -->
<svg class="slide col-right row-2" viewBox="0 0 804 452" aria-label="Timeline slide">
  <rect width="804" height="452" fill="#fff"/>
  <text class="heading" x="402" y="45" font-size="36" text-anchor="middle">Timeline Slide Goes Here</text>
  <rect x="377" y="66" width="50" height="5" fill="var(--accent)"/>
  <line x1="31" y1="226" x2="765" y2="226" stroke="var(--sky)" stroke-width="6"/>
  <circle cx="214" cy="226" r="11" fill="var(--sky)"/>
  <circle cx="398" cy="226" r="11" fill="var(--sky)"/>
  <circle cx="582" cy="226" r="11" fill="var(--sky)"/>
  <polygon points="121,180 65,274 177,274" fill="var(--navy)"/>
  <polygon points="249,180 361,180 305,274" fill="var(--navy)"/>
  <polygon points="486,180 430,274 542,274" fill="var(--navy)"/>
  <polygon points="619,180 731,180 675,274" fill="var(--navy)"/>
  <g class="label" fill="#fff" font-size="19" text-anchor="middle">
    <text x="121" y="253">2021</text><text x="305" y="208">2022</text><text x="486" y="253">2023</text><text x="675" y="211">2024</text>
  </g>
  <g class="label" fill="var(--navy)" font-size="15.5" text-anchor="middle">
    <text x="121" y="111">Nemo enim ipsam</text><text x="486" y="111">Nemo enim ipsam</text>
    <text x="305" y="300">Nemo enim ipsam</text><text x="675" y="300">Nemo enim ipsam</text>
  </g>
  <g class="body" font-size="11" text-anchor="middle">
    <text><tspan x="121" y="131">Excepteur sint occaecat</tspan><tspan x="121" y="147">cupidatat non proident, sunt</tspan><tspan x="121" y="163">in culpa qui offic.</tspan></text>
    <text><tspan x="486" y="131">Excepteur sint occaecat</tspan><tspan x="486" y="147">cupidatat non proident, sunt</tspan><tspan x="486" y="163">in culpa qui offic.</tspan></text>
    <text><tspan x="305" y="320">Excepteur sint occaecat</tspan><tspan x="305" y="336">cupidatat non proident, sunt</tspan><tspan x="305" y="352">in culpa qui offic.</tspan></text>
    <text><tspan x="675" y="320">Excepteur sint occaecat</tspan><tspan x="675" y="336">cupidatat non proident, sunt</tspan><tspan x="675" y="352">in culpa qui offic.</tspan></text>
  </g>
  <rect class="footer-band" y="415" width="804" height="37"/>
  <text class="brand" x="19" y="439" font-size="15">VANTRIX</text>
  <rect x="88" y="429" width="8" height="8" fill="var(--accent)"/>
  <circle class="page-dot" cx="782" cy="426" r="10"/><text class="page-num" x="782" y="430" text-anchor="middle">6</text>
</svg>

<!-- Title & content -->
<svg class="slide col-left row-3" viewBox="0 0 804 452" aria-label="Title and content slide">
  <defs>
    <linearGradient id="content-photo-a" x1="0" y1="0" x2="1" y2="1"><stop offset="0" stop-color="#e6ecf2"/><stop offset="1" stop-color="#2a3443"/></linearGradient>
    <linearGradient id="content-photo-b" x1="0" y1="0" x2="1" y2="1"><stop offset="0" stop-color="#dfe4ea"/><stop offset="1" stop-color="#8d97a4"/></linearGradient>
  </defs>
  <rect width="804" height="452" fill="#fff"/>
  <polygon points="406,0 728,0 569,272" fill="url(#content-photo-a)" role="img" aria-label="Photo of two business colleagues reviewing a tablet"/>
  <polygon points="719,87 502,415 804,415 804,87" fill="url(#content-photo-b)" role="img" aria-label="Photo of a businesswoman in a bright office"/>
  <text class="heading" font-size="36"><tspan x="23" y="63">Title &amp; Content Slide</tspan><tspan x="23" y="99">Goes Here</tspan></text>
  <rect x="23" y="116" width="50" height="5" fill="var(--accent)"/>
  <text class="body" font-size="8.7" fill="var(--ink)">
    <tspan x="23" y="162">Sed ut perspiciatis unde omnis iste natus error sit voluptatem accusantium</tspan>
    <tspan x="23" y="177">doloremque laudantium, totam rem aperiam, eaque ipsa quae ab illo inventore</tspan>
    <tspan x="23" y="192">veritatis et quasi architecto beatae vitae dicta sunt explicabo. Nemo enim ipsam</tspan>
    <tspan x="23" y="207">voluptatem quia voluptas sit aspernatur aut odit aut fugit, sed quia consequuntur</tspan>
    <tspan x="23" y="222">magni dolores eos qui ratione voluptatem sequi nesciunt. Neque porro quisquam</tspan>
    <tspan x="23" y="237">est, qui dolorem ipsum quia dolor sit amet, consectetur, adipisci velit, sed quia non</tspan>
    <tspan x="23" y="252">numquam eius modi tempora incidunt ut labore et dolore magnam aliquam</tspan>
    <tspan x="23" y="267">quaerat voluptatem.</tspan>
    <tspan x="23" y="297">Sed ut perspiciatis unde omnis iste natus error sit voluptatem accusantium</tspan>
    <tspan x="23" y="312">doloremque laudantium, totam rem aperiam, eaque ipsa quae ab illo inventore</tspan>
    <tspan x="23" y="327">veritatis et quasi architecto beatae vitae dicta sunt explicabo. Nemo enim ipsam</tspan>
    <tspan x="23" y="342">voluptatem quia voluptas sit aspernatur aut odit aut fugit, sed quia consequuntur</tspan>
    <tspan x="23" y="357">magni dolores eos qui ratione voluptatem sequi nesciunt. Neque porro quisquam</tspan>
    <tspan x="23" y="372">est, qui dolorem ipsum quia dolor sit amet, consectetur, adipisci velit, sed quia non</tspan>
    <tspan x="23" y="387">numquam eius modi tempora incidunt.</tspan>
  </text>
  <rect class="footer-band" y="415" width="804" height="37"/>
  <text class="brand" x="10" y="439" font-size="15">VANTRIX</text>
  <rect x="79" y="429" width="8" height="8" fill="var(--accent)"/>
  <circle class="page-dot" cx="781" cy="434" r="10"/><text class="page-num" x="781" y="438" text-anchor="middle">3</text>
</svg>

<!-- Break -->
<svg class="slide col-right row-3" viewBox="0 0 804 452" aria-label="Break slide">
  <defs>
    <linearGradient id="break-bg" x1="0" y1="0" x2="1" y2="1"><stop offset="0" stop-color="#d3e4f2"/><stop offset="0.5" stop-color="#c6dcee"/><stop offset="1" stop-color="#cfe1f0"/></linearGradient>
  </defs>
  <rect width="804" height="452" fill="url(#break-bg)" role="img" aria-label="Soft light blue background with a flowing particle wave"/>
  <text class="heading" x="402" y="189" font-size="36" text-anchor="middle">Break Slide Goes Here</text>
  <rect x="377" y="211" width="50" height="5" fill="var(--accent)"/>
  <text class="body" font-size="16" text-anchor="middle" fill="var(--ink)"><tspan x="402" y="260">Sed ut perspiciatis unde omnis iste natus error sit voluptatem</tspan><tspan x="402" y="288">accusantium doloremque laudantium.</tspan></text>
  <text class="brand" x="19" y="439" font-size="15">VANTRIX</text>
  <rect x="88" y="429" width="8" height="8" fill="var(--accent)"/>
  <circle class="page-dot" cx="782" cy="429" r="10"/><text class="page-num" x="782" y="433" text-anchor="middle">7</text>
</svg>

<!-- Four content -->
<svg class="slide col-left row-4" viewBox="0 0 804 452" aria-label="Four content slide">
  <rect width="804" height="452" fill="#fff"/>
  <text class="heading" font-size="36" text-anchor="middle"><tspan x="402" y="55">Here Content Slide</tspan><tspan x="402" y="92">Goes Here</tspan></text>
  <rect x="377" y="111" width="50" height="5" fill="var(--accent)"/>
  <rect x="11" y="149" width="187" height="246" fill="var(--navy)"/>
  <rect x="209" y="149" width="187" height="246" fill="var(--ocean)"/>
  <rect x="406" y="149" width="187" height="246" fill="var(--sky)"/>
  <rect x="604" y="149" width="187" height="246" fill="var(--mist)"/>
  <polygon points="54,168 155,168 104,253" fill="#fff"/>
  <polygon points="302,168 252,253 353,253" fill="#fff"/>
  <polygon points="449,168 550,168 499,253" fill="#fff"/>
  <polygon points="697,168 647,253 748,253" fill="#fff"/>
  <g class="icon dark"><circle cx="104" cy="187" r="6"/><path d="M95 206 q9 -10 18 0"/></g>
  <g class="icon dark"><rect x="289" y="214" width="26" height="17" rx="1"/><path d="M302 231 v5 M296 236 h12"/></g>
  <g class="icon dark"><rect x="488" y="181" width="22" height="14" rx="1"/><path d="M493 191 v-3 M498 191 v-5 M503 191 v-7"/></g>
  <g class="icon dark"><rect x="685" y="212" width="24" height="16" rx="1"/><circle cx="697" cy="220" r="4"/></g>
  <g class="label" font-size="14.5" text-anchor="middle">
    <text fill="#fff"><tspan x="104" y="287">Excepteur sint</tspan><tspan x="104" y="307">occaecat</tspan></text>
    <text fill="#fff"><tspan x="302" y="287">Excepteur sint</tspan><tspan x="302" y="307">occaecat</tspan></text>
    <text fill="#fff"><tspan x="499" y="287">Excepteur sint</tspan><tspan x="499" y="307">occaecat</tspan></text>
    <text fill="var(--navy)"><tspan x="697" y="287">Excepteur sint</tspan><tspan x="697" y="307">occaecat</tspan></text>
  </g>
  <g class="body" font-size="10.5" text-anchor="middle">
    <text fill="#fff"><tspan x="104" y="328">Duis aute irure dolor in rep</tspan><tspan x="104" y="344">rehenderit in voluptate velit</tspan><tspan x="104" y="360">esse cillum dolore eu fugiat</tspan><tspan x="104" y="376">nulla pariatur</tspan></text>
    <text fill="#fff"><tspan x="302" y="328">Duis aute irure dolor in rep</tspan><tspan x="302" y="344">rehenderit in voluptate velit</tspan><tspan x="302" y="360">esse cillum dolore eu fugiat</tspan><tspan x="302" y="376">nulla pariatur</tspan></text>
    <text fill="#fff"><tspan x="499" y="328">Duis aute irure dolor in rep</tspan><tspan x="499" y="344">rehenderit in voluptate velit</tspan><tspan x="499" y="360">esse cillum dolore eu fugiat</tspan><tspan x="499" y="376">nulla pariatur</tspan></text>
    <text fill="var(--ink)"><tspan x="697" y="328">Duis aute irure dolor in rep</tspan><tspan x="697" y="344">rehenderit in voluptate velit</tspan><tspan x="697" y="360">esse cillum dolore eu fugiat</tspan><tspan x="697" y="376">nulla pariatur</tspan></text>
  </g>
  <rect class="footer-band" y="415" width="804" height="37"/>
  <text class="brand" x="10" y="439" font-size="15">VANTRIX</text>
  <rect x="79" y="429" width="8" height="8" fill="var(--accent)"/>
  <circle class="page-dot" cx="779" cy="434" r="10"/><text class="page-num" x="779" y="438" text-anchor="middle">4</text>
</svg>

<!-- Closing -->
<svg class="slide col-right row-4" viewBox="0 0 804 452" aria-label="Closing slide">
  <defs>
    <linearGradient id="closing-bg" x1="0" y1="0" x2="1" y2="1"><stop offset="0" stop-color="#0a4fa3"/><stop offset="0.55" stop-color="#0054AA"/><stop offset="1" stop-color="#1f6fc4"/></linearGradient>
  </defs>
  <rect width="804" height="452" fill="url(#closing-bg)" role="img" aria-label="Deep blue background with abstract flowing curves"/>
  <rect x="377" y="135" width="50" height="5" fill="#fff"/>
  <text class="heading light" x="402" y="188" font-size="40" text-anchor="middle">Thank You</text>
  <text class="body light" font-size="15.5" text-anchor="middle"><tspan x="402" y="229">Sed ut perspiciatis unde omnis iste natus error ptatem accusantium doloremque</tspan><tspan x="402" y="257">laudantiu mexercitation ullamco laboris nisi ut aliquip.</tspan></text>
  <g fill="none" stroke="#fff" stroke-width="1.5">
    <circle cx="338" cy="302" r="18"/><circle cx="401" cy="302" r="18"/><circle cx="468" cy="302" r="18"/>
  </g>
</svg>

</body>
</html>
```